Halvery Construction Group Website

Need a dynamic corporate website that can be built on with time. We want to get our information out to the world and have a place where customers can submit requests for proposals.

Target Market(s)

Custom home owners and buyers. Architects and Real Estate Agents.

Industry/Entity Type

Construction

Number of Pages Required

3 page

Font styles to use
Serif
Sans Serif

Requirements
Must have
• Company logo, about, company contact information, biography, contact, projects,
• Sleek, modern, clean, attractive design.
• Online form customers can use for filling out a request for project proposal.
• Linkedin hyperlink.
• Uses www.halveryconstructiongroup.example

```html
<!DOCTYPE html>
<html lang="en">
<head>
<meta charset="utf-8">
<title>Halvery Construction Group</title>
<link href="https://fonts.googleapis.com/css2?family=Lato:wght@300;400;700;900&family=Michroma&display=swap" rel="stylesheet">
<style>
:root{
  --navy:#27377a;
  --blue:#1f5fae;
  --sky:#2f8fd0;
  --ink:#222;
  --muted:#666;
  --soft:#f4f4f4;
  --line:#e3e3e3;
  --footer:#2e2e2e;
  --footer-dark:#1d1d1d;
  --white:#fff;
  --client:#8f8f8f;
  --client-faint:#cfcfcf;
}
*{margin:0;padding:0;box-sizing:border-box}
html,body{width:1200px;height:3220px;overflow:hidden}
body{position:relative;font-family:"Lato",sans-serif;color:var(--ink);background:var(--white)}
.abs{position:absolute}

/* hero */
.hero{left:0;top:0;width:1200px;height:676px;background:linear-gradient(180deg,#c9d8e6 0%,#8aa7bf 30%,#3f6a8a 55%,#6a6a5a 75%,#a9573d 100%)}
.topline{left:0;top:0;width:1200px;height:3px;background:var(--navy)}
.brand{left:77px;top:17px;display:flex;align-items:center;gap:12px}
.brand-mark{width:62px;height:62px;background:var(--navy)}
.brand-name{font-family:"Michroma",sans-serif;color:var(--navy);font-size:36px;line-height:1;letter-spacing:1px}
.brand-sub{font-family:"Lato",sans-serif;color:var(--navy);font-size:13px;letter-spacing:.5px;margin-top:4px}
.nav{left:663px;top:0;display:flex;height:95px}
.nav a{display:flex;align-items:center;justify-content:center;font-size:16px;color:#1b2230;text-decoration:none;padding:0 32px;letter-spacing:.5px}
.nav a.active{background:var(--blue);color:var(--white);width:82px;padding:0}
.hero-title{right:82px;top:200px;text-align:right;color:var(--white);font-weight:700;font-size:56px;line-height:75px;text-shadow:0 2px 6px rgba(0,0,0,.35)}
.arrow{width:41px;height:86px;top:296px;background:var(--navy);display:flex;align-items:center;justify-content:center}
.arrow.left{left:0;background:rgba(255,255,255,.25)}
.arrow.right{right:0}
.estimate{left:67px;top:490px;width:1067px;height:135px;background:rgba(255,255,255,.35);border:1px solid rgba(255,255,255,.6)}
.estimate h2{position:absolute;left:0;right:0;top:18px;text-align:center;font-family:"Michroma",sans-serif;font-weight:400;font-size:22px;color:#111}
.field{position:absolute;top:59px;height:43px;background:var(--white);font-size:12px;color:#333;padding:14px 10px}
.submit{position:absolute;top:59px;left:961px;width:86px;height:43px;background:var(--sky);color:var(--white);font-size:15px;font-weight:700;display:flex;align-items:center;justify-content:center}

/* welcome */
.welcome-title{left:0;top:728px;width:1200px;text-align:center;font-family:"Michroma",sans-serif;font-size:37px;color:#1a1a1a}
.welcome-title span{color:var(--blue)}
.welcome-sub{left:0;top:774px;width:1200px;text-align:center;font-size:19px;color:#555;letter-spacing:.5px}
.lead{left:172px;top:814px;width:858px;text-align:center;font-size:13.5px;line-height:22px;color:#555}
.divider{left:348px;top:900px;width:485px;height:76px}
.divider .label{position:absolute;top:28px;font-size:15px;color:#222;letter-spacing:.5px}
.lead2{left:250px;top:1010px;width:700px;text-align:center;font-size:13.5px;line-height:22px;color:#555}
.card{top:1084px;width:333px}
.card .photo{height:166px}
.card h3{font-weight:400;font-size:20px;text-align:center;margin-top:18px;color:#222}
.card p{font-size:13.5px;line-height:22px;text-align:center;color:#555;margin-top:6px}
.btn{display:inline-flex;align-items:center;justify-content:center;background:var(--navy);color:var(--white);font-size:14px;text-decoration:none}
.card .btn{width:114px;height:41px;margin:16px auto 0;display:flex}

/* features */
.band{left:0;width:1200px}
.band.grey{background:var(--soft)}
.feat-title{font-size:24px;font-weight:700;color:#111}
.feat-text{font-size:14px;line-height:23px;color:#333;margin-top:14px}

/* clients */
.clients-title{left:0;top:2590px;width:1200px;text-align:center;font-size:42px;font-weight:400;letter-spacing:1px;color:#222}
.client{width:170px;height:107px;border:1px solid #efefef;background:var(--white);display:flex;align-items:center;justify-content:center;gap:8px;font-size:24px;font-weight:700;color:var(--client);white-space:nowrap}
.client .dot{width:12px;height:12px;border-radius:50%;background:var(--client);flex:none}
.client.faded{color:var(--client-faint)}
.client.faded .dot{background:var(--client-faint)}

/* footer */
.footer{left:0;top:2930px;width:1200px;height:237px;background:var(--footer);color:#ddd}
.footer-mark{position:absolute;left:77px;top:39px;width:166px;height:166px;background:#4a4a4a;display:flex;align-items:center;justify-content:center;font-size:24px;font-weight:700;color:#bdbdbd;letter-spacing:1px}
.fcol{position:absolute;top:38px}
.fcol h4{font-size:17px;font-weight:400;letter-spacing:.5px;color:var(--white);margin-bottom:18px}
.fline{display:flex;gap:14px;font-size:13.5px;line-height:21px;margin-bottom:16px}
.news{display:flex;gap:14px;margin-bottom:16px}
.avatar{width:50px;height:50px;border-radius:50%;background:linear-gradient(#b9a58c,#7a6a58);flex:none}
.news p{font-size:13.5px;line-height:20px;color:#eee}
.news small{display:block;font-size:10.5px;color:#999}
.links a{display:block;font-size:13.5px;color:#ccc;text-decoration:none;line-height:31px}
.bottom{left:0;top:3167px;width:1200px;height:53px;background:var(--footer-dark);display:flex;align-items:center;padding:0 82px;font-size:13.5px;color:#ccc}
.bottom span{color:var(--sky)}
.social{position:absolute;right:79px;top:11px;display:flex;gap:11px}
.social i{width:30px;height:30px;border-radius:50%;background:var(--blue);display:block}
</style>
</head>
<body>

<!-- HERO -->
<section class="abs hero" role="img" aria-label="Coastal hillside town with red-tiled roofs, pine trees and the sea under a pale sky"></section>
<div class="abs topline"></div>
<div class="abs brand">
  <div class="brand-mark"></div>
  <div>
    <div class="brand-name">HALVERY</div>
    <div class="brand-sub">CONSTRUCTION GROUP, INC.</div>
  </div>
</div>
<nav class="abs nav">
  <a href="#" class="active">HOME</a>
  <a href="#">ABOUT</a>
  <a href="#">PROJECTS</a>
  <a href="#">CONTACT</a>
</nav>
<h1 class="abs hero-title">Let us keep you up to<br>date with our latest<br>developments.</h1>
<div class="abs arrow left"><svg width="14" height="24"><path d="M12 2 2 12l10 10" fill="none" stroke="#fff" stroke-width="2"/></svg></div>
<div class="abs arrow right"><svg width="14" height="24"><path d="M2 2l10 10L2 22" fill="none" stroke="#fff" stroke-width="2"/></svg></div>
<form class="abs estimate">
  <h2>Request a Free Estimate</h2>
  <div class="field" style="left:19px;width:193px">First Name</div>
  <div class="field" style="left:223px;width:195px">Last Name</div>
  <div class="field" style="left:429px;width:305px">E-Mail Address</div>
  <div class="field" style="left:742px;width:207px">Phone No.</div>
  <div class="submit">SUBMIT</div>
</form>

<!-- WELCOME -->
<h2 class="abs welcome-title">WELCOME TO <span>HALVERY</span></h2>
<div class="abs welcome-sub">CONSTRUCTION GROUP, INC.</div>
<p class="abs lead">Lorem Ipsum is simply dummy text of the printing and typesetting industry. Lorem Ipsum has been the industry's standard dummy text ever since the 1500s, when an unknown printer took a galley of type and scrambled it to make a type specimen book. It has survived not only five centuries, but also the leap into electronic typesetting, remaining essentially unchanged.</p>
<div class="abs divider">
  <svg width="485" height="76" class="abs" style="left:0;top:0">
    <line x1="0" y1="53" x2="215" y2="53" stroke="#1f5fae" stroke-width="2"/>
    <line x1="291" y1="53" x2="485" y2="53" stroke="#1f5fae" stroke-width="2"/>
    <circle cx="253" cy="38" r="36" fill="#fff" stroke="#1f5fae" stroke-width="2"/>
    <path d="M243 30l10 9 10-9M243 40l10 9 10-9" fill="none" stroke="#1f5fae" stroke-width="2.5"/>
  </svg>
  <span class="label" style="left:27px">CHECK OUT OUR</span>
  <span class="label" style="left:306px">DEVELOPMENT</span>
</div>
<p class="abs lead2">Lorem Ipsum is simply dummy text of the printing and typesetting industry. Lorem Ipsum has been the industry's standard dummy text ever since the 1500s</p>

<article class="abs card" style="left:77px">
  <div class="photo" role="img" aria-label="Modern two-storey house with stone cladding and a lawn" style="background:linear-gradient(180deg,#8fb8e0 0%,#c9d6e0 45%,#5b5b5b 70%,#6a9a45 100%)"></div>
  <h3>Project Title</h3>
  <p>Lorem Ipsum is simply dummy text of the printing<br>and typesetting industry.</p>
  <a href="#" class="btn">View Project</a>
</article>
<article class="abs card" style="left:434px">
  <div class="photo" role="img" aria-label="City skyline lit up at night" style="background:linear-gradient(180deg,#1c1a2a 0%,#4a3020 50%,#c9822e 80%,#3a2a24 100%)"></div>
  <h3>Project Title</h3>
  <p>Lorem Ipsum is simply dummy text of the printing<br>and typesetting industry.</p>
  <a href="#" class="btn">View Project</a>
</article>
<article class="abs card" style="left:790px">
  <div class="photo" role="img" aria-label="Waterfront apartment buildings beside a lawn" style="background:linear-gradient(180deg,#a9c8e6 0%,#e8e2d2 45%,#9aa7a8 70%,#5f8f3f 100%)"></div>
  <h3>Project Title</h3>
  <p>Lorem Ipsum is simply dummy text of the printing<br>and typesetting industry.</p>
  <a href="#" class="btn">View Project</a>
</article>

<!-- SMALL & LARGE BUILDING -->
<section class="abs band grey" style="top:1449px;height:365px">
  <div class="abs" role="img" aria-label="Isometric illustration of a multi-storey building under construction on a city block" style="left:125px;top:24px;width:412px;height:280px;border-radius:40px;background:radial-gradient(ellipse at center,#d98a4a 0%,#9aa0a6 55%,rgba(244,244,244,0) 75%)"></div>
  <div class="abs" style="left:644px;top:72px;width:420px">
    <h3 class="feat-title">Small &amp; Large Building</h3>
    <p class="feat-text">Designed for lifestyle is the real reason you have a home, memoriLorem Ipsum is simply dummy text of the printing and typesetting industry. Lorem Ipsum has been the industry's standard dummy text ever.</p>
    <a href="#" class="btn" style="width:240px;height:50px;margin-top:20px;font-size:19px">View Developments</a>
  </div>
</section>

<!-- PERFECT CONSTRUCTION PLANS -->
<section class="abs band" style="top:1814px;height:365px">
  <div class="abs" style="left:150px;top:72px;width:473px;text-align:right">
    <h3 class="feat-title" style="font-weight:400;font-size:24px">Perfect Construction Plans</h3>
    <p class="feat-text">Our unique approach to building starts with extensive resLorem Ipsum is simply dummy text of the printing and typesetting industry. Lorem Ipsum has been the industry's standard dummy text ever since the 1500s, when an unknown printer took a galley of type and scrambled it to make.</p>
    <a href="#" class="btn" style="width:155px;height:52px;margin-top:24px;font-size:19px">Get Started</a>
  </div>
  <div class="abs" role="img" aria-label="Illustration of a small house model with a hard hat on rolled blueprints" style="left:683px;top:43px;width:477px;height:301px;border-radius:50%;background:radial-gradient(ellipse at center,#2f8fd0 0%,#5fb0e6 45%,rgba(255,255,255,0) 72%)"></div>
</section>

<!-- TEAM WORK -->
<section class="abs band grey" style="top:2179px;height:365px">
  <div class="abs" role="img" aria-label="Three construction workers in hard hats standing together" style="left:64px;top:32px;width:580px;height:333px;background:linear-gradient(90deg,rgba(244,244,244,0) 0%,#c9bfae 25%,#8c8778 60%,rgba(244,244,244,0) 100%)"></div>
  <div class="abs" style="left:644px;top:100px;width:440px">
    <h3 class="feat-title">The Effective Team Work</h3>
    <p class="feat-text" style="margin-top:10px">Lorem Ipsum is simply dummy text of the printing and typesetting industry. Lorem Ipsum has been the industry's standard dummy text ever since the 1500s, when an unknown printer took a galley of type and scrambled it to make a type specimen book.</p>
  </div>
</section>

<!-- CLIENTS -->
<h2 class="abs clients-title">OUR CLIENTS</h2>
<div class="abs client" style="left:82px;top:2656px"><i class="dot"></i>Bramwell</div>
<div class="abs client" style="left:255px;top:2656px">Fenmoor</div>
<div class="abs client" style="left:428px;top:2656px">Kelmont</div>
<div class="abs client" style="left:602px;top:2656px"><i class="dot"></i>Duvessa</div>
<div class="abs client" style="left:775px;top:2656px">Pinewold</div>
<div class="abs client" style="left:948px;top:2656px">Tavrin</div>
<div class="abs client faded" style="left:82px;top:2770px"><i class="dot"></i>Bramwell</div>
<div class="abs client faded" style="left:255px;top:2770px">Fenmoor</div>
<div class="abs client faded" style="left:428px;top:2770px">Kelmont</div>
<div class="abs client faded" style="left:602px;top:2770px"><i class="dot"></i>Duvessa</div>
<div class="abs client faded" style="left:775px;top:2770px">Pinewold</div>
<div class="abs client faded" style="left:948px;top:2770px">Tavrin</div>

<!-- FOOTER -->
<footer class="abs footer">
  <div class="footer-mark">HALVERY</div>
  <div class="fcol" style="left:344px;width:230px">
    <h4>CONTACT INFO</h4>
    <div class="fline">
      <svg width="22" height="20"><path d="M2 4l6-2 6 2 6-2v14l-6 2-6-2-6 2z M8 2v14 M14 4v14" fill="none" stroke="#ddd" stroke-width="1.5"/></svg>
      <span>CORPORATE OFFICE<br>123 Building Name, Street ,<br>City, Country - Zipcode</span>
    </div>
    <div class="fline">
      <svg width="22" height="20"><path d="M4 2h4l2 5-3 2c1 3 3 5 6 6l2-3 5 2v4c0 1-1 2-2 2C9 20 2 13 2 4c0-1 1-2 2-2z" fill="none" stroke="#ddd" stroke-width="1.5"/></svg>
      <span>123-4567-890</span>
    </div>
    <div class="fline">
      <svg width="22" height="20"><rect x="2" y="4" width="18" height="13" fill="none" stroke="#ddd" stroke-width="1.5"/><path d="M2 4l9 7 9-7" fill="none" stroke="#ddd" stroke-width="1.5"/></svg>
      <span>info@halverygroup.example</span>
    </div>
  </div>
  <div class="fcol" style="left:610px;width:220px">
    <h4>NEWS FEED</h4>
    <div class="news"><div class="avatar" role="img" aria-label="News author photo"></div><p>Lorem Ipsum is simply<br>dummy text of<small>Today 5:60 pm - 12.06.2016</small></p></div>
    <div class="news"><div class="avatar" role="img" aria-label="News author photo"></div><p>Lorem Ipsum is simply<br>dummy text of<small>Today 2:10 pm - 12.06.2016</small></p></div>
  </div>
  <div class="fcol links" style="left:874px;width:200px">
    <h4 style="margin-bottom:8px">USEFUL LINKS</h4>
    <a href="#" style="color:#fff">» Home</a>
    <a href="#">» About</a>
    <a href="#">» Projects</a>
    <a href="#">» Clients</a>
    <a href="#">» Contact</a>
  </div>
</footer>
<div class="abs bottom">
  <p>© <span>HALVERY CONSTRUCTION GROUP</span> - 2016. All Rights Reserved</p>
  <div class="social"><i></i><i></i><i></i><i></i><i></i></div>
</div>

</body>
</html>
```